Consulting Website

We are looking at renewing out company's website. we are an organizational development consulting firm that works within the Middle East and Africa. Our focus on on organizations within the Gulf area.

We are looking to having a simple, clean and attractive website. pictures should be relevant to our location.

We are also looking for a creative design, something that isn't just "another consulting website"
Updates

Thank you all for submitting your designs, following are some general comments;

- Having a veiled women on the intro is NOT a must
- have a picture with people is NOT a must too, we can use nature, symbols, places..anything really!
- Here are some sites i like;
brightvale.com
http://www.lanternhomesgroup.com/
http://www.pelicandraft.com/
http://www.morvenli.lk/

I hope these could give you some idea :)

thanks again.

Industry/Entity Type

It Company

Requirements
Must have
• Tabs for press, testimonials, products, resources and services.
pictures also should be relevant to the geographical location. i.e. veiled women, men in traditional costumes and so on.

It's very important that we MAINTAIN the corporate colors of the logo.
Should not have
• Clean and neat design!
i REALLY dont like crowded designs.

```html
<!DOCTYPE html>
<html lang="en">
<head>
<meta charset="utf-8">
<title>Noravi Consulting</title>
<link rel="stylesheet" href="https://fonts.googleapis.com/css2?family=Open+Sans:wght@400;600;700&family=Cinzel:wght@400&family=Arimo:wght@400&display=swap">
<style>
  :root {
    --page-bg: #637a88;
    --sheet: #ffffff;
    --ink: #2b2f45;
    --body-text: #4a4a4a;
    --slate: #5d6f7c;
    --nav-btn: #d3d6d2;
    --nav-band: #e9ebe8;
    --frame: #c9a39a;
    --photo-dark: #1c2138;
    --photo-mid: #2f3655;
    --rule: #c8c8c8;
    --footer: #262b40;
    --footer-text: #c3c6d0;
    --footer-head: #b9bcc8;
    --blue-btn: #3a74b0;
    --blue-btn-dark: #23558c;
    --grey-btn: #bdbdbd;
  }
  * { margin: 0; padding: 0; box-sizing: border-box; }
  html, body { width: 1200px; height: 1062px; overflow: hidden; }
  body {
    position: relative;
    background: var(--page-bg);
    font-family: "Open Sans", sans-serif;
    color: var(--body-text);
  }
  .sheet {
    position: absolute; left: 65px; top: 0; width: 1071px; height: 870px;
    background: var(--sheet);
  }
  .brand {
    position: absolute; display: flex; align-items: center; gap: 10px;
  }
  .brand-square { width: 46px; height: 46px; background: var(--slate); }
  .brand-name {
    font-family: "Open Sans", sans-serif; font-weight: 400;
    color: var(--slate); font-size: 24px; letter-spacing: 1px; line-height: 1;
  }
  .brand--header { left: 96px; top: 40px; }
  .search {
    position: absolute; left: 826px; top: 53px; width: 275px; height: 31px;
    border: 1px solid #cfd3d6; background: #fff;
    font-family: Arimo, sans-serif; font-size: 13px; color: #2a3a5a;
    padding: 7px 12px;
  }
  .search svg { position: absolute; right: 9px; top: 7px; }
  .nav-band {
    position: absolute; left: 110px; top: 115px; width: 1020px; height: 62px;
    background: linear-gradient(90deg, rgba(233,235,232,0) 0%, var(--nav-band) 6%, var(--nav-band) 94%, rgba(233,235,232,0) 100%);
  }
  .nav-btn {
    position: absolute; top: 129px; width: 101px; height: 31px;
    background: var(--nav-btn); border-radius: 4px;
    font-family: Arimo, sans-serif; font-size: 15px; color: #1e2230;
    text-align: center; line-height: 31px;
  }
  .hero {
    position: absolute; left: 152px; top: 185px; width: 886px; height: 346px;
    border: 4px solid var(--frame);
    background: radial-gradient(ellipse at 35% 45%, var(--photo-mid), var(--photo-dark) 70%);
  }
  .hero-arrow { position: absolute; top: 323px; }
  .intro-title {
    position: absolute; left: 157px; top: 553px;
    font-size: 18px; font-weight: 700; color: var(--ink);
  }
  .intro-text {
    position: absolute; left: 157px; top: 596px; width: 536px;
    font-size: 12.6px; line-height: 19px; color: var(--body-text);
  }
  .btn-read {
    position: absolute; left: 526px; top: 781px; width: 149px; height: 31px;
    border: 1px solid #d4d4d4; border-radius: 3px;
    background: linear-gradient(#cfcfcf, #a9a9a9);
    color: #fff; font-weight: 600; font-size: 13.5px;
    padding: 5px 0 0 28px;
  }
  .btn-read svg { position: absolute; right: 22px; top: 10px; }
  .news-title {
    position: absolute; left: 755px; top: 541px;
    font-family: Cinzel, serif; font-size: 16px; color: var(--ink);
  }
  .rule { position: absolute; height: 0; border-top: 1px dashed var(--rule); }
  .news-item { position: absolute; left: 756px; width: 282px; display: flex; gap: 8px; }
  .news-thumb {
    width: 54px; height: 50px; flex: none;
    border: 1px solid #cfcfcf; border-radius: 3px; padding: 5px; background: #f4f4f4;
  }
  .news-thumb span { display: block; width: 100%; height: 100%; }
  .news-text {
    font-family: Arimo, sans-serif; font-size: 11.2px; line-height: 12.5px; color: #333;
    padding-top: 0;
  }
  .btn-blue {
    position: absolute; height: 30px;
    background: linear-gradient(var(--blue-btn), var(--blue-btn-dark));
    border: 1px solid #1c4a7c; border-radius: 2px;
    color: #fff; font-family: Cinzel, serif; font-size: 12.5px; text-transform: none;
    padding: 6px 0 0 12px;
  }
  .btn-blue svg { position: absolute; right: 10px; top: 12px; }
  .footer {
    position: absolute; left: 0; top: 870px; width: 1200px; height: 192px;
    background: var(--footer);
  }
  .footer-head {
    position: absolute; font-family: Cinzel, serif; font-size: 17px; color: var(--footer-head);
  }
  .footer-rule { position: absolute; border-top: 1px dashed var(--footer-text); height: 0; }
  .footer-text {
    position: absolute; font-size: 11.2px; line-height: 15px; color: var(--footer-text); width: 320px;
  }
  .email-field {
    position: absolute; left: 95px; top: 964px; width: 308px; height: 34px;
    background: #fff; border-radius: 4px; border: 1px solid #9aa0ad;
    font-size: 11px; color: #c8c8c8; letter-spacing: 1px; padding: 8px 13px;
  }
  .social { position: absolute; left: 514px; top: 966px; display: flex; gap: 8px; }
  .social span { width: 42px; height: 42px; border-radius: 7px; display: block; }
  .brand--footer {
    left: 888px; top: 932px; width: 246px; height: 62px; background: #fff;
    padding: 0 10px; gap: 8px;
  }
  .brand--footer .brand-square { width: 42px; height: 42px; }
  .brand--footer .brand-name { font-size: 20px; }
</style>
</head>
<body>
  <div class="sheet"></div>

  <div class="brand brand--header">
    <span class="brand-square"></span>
    <span class="brand-name">NORAVI CONSULTING</span>
  </div>

  <div class="search">Search
    <svg width="14" height="14" viewBox="0 0 14 14"><circle cx="5.5" cy="5.5" r="4" fill="none" stroke="#888" stroke-width="1.8"/><line x1="8.5" y1="8.5" x2="13" y2="13" stroke="#888" stroke-width="2.4"/></svg>
  </div>

  <div class="nav-band"></div>
  <div class="nav-btn" style="left:264px">Home</div>
  <div class="nav-btn" style="left:378px">About</div>
  <div class="nav-btn" style="left:494px">Services</div>
  <div class="nav-btn" style="left:608px">Projects</div>
  <div class="nav-btn" style="left:723px">News</div>
  <div class="nav-btn" style="left:839px">Contacts</div>

  <div class="hero" role="img" aria-label="Slideshow photo: veiled women in dark abayas gathered together"></div>
  <svg class="hero-arrow" style="left:128px" width="21" height="56" viewBox="0 0 21 56"><polygon points="21,0 0,28 21,56 15,28" fill="#1f2440"/></svg>
  <svg class="hero-arrow" style="left:1041px" width="21" height="56" viewBox="0 0 21 56"><polygon points="0,0 21,28 0,56 6,28" fill="#1f2440"/></svg>

  <h1 class="intro-title">Noravi Consulting</h1>
  <p class="intro-text">Noravi Consulting is a firm specialized in providing customized Organization Development solutions to companies in the Middle East and Africa. Recognizing the inability of imported models and solutions to solve problems that face companies in our region, Noravi Consulting builds on international best practices and customizes them to create best-fit solutions that are capable of addressing challenges effectively. Noravi Consulting provides Organization Development solutions addressing the "HOW – Soft Side" that is needed to achieve the "WHAT – Business Strategy" in a holistic manner. Noravi Consulting work centers around building an organizational culture that is aligned with and supports the business strategy.</p>
  <div class="btn-read">Read more
    <svg width="14" height="12" viewBox="0 0 14 12"><polygon points="0,0 14,6 0,12 3,6" fill="#fff"/></svg>
  </div>

  <h2 class="news-title">News Updates</h2>
  <div class="rule" style="left:755px;top:568px;width:282px"></div>

  <div class="news-item" style="top:580px">
    <div class="news-thumb"><span role="img" aria-label="News thumbnail, orange and blue graphic" style="background:linear-gradient(135deg,#3a5fb0,#e07a2a)"></span></div>
    <p class="news-text">Lorem ipsum dolor sit amet, consectetur adipisicing elit, sed do eiusmod tempor incididunt ut labore et dolore magna aliqua.</p>
  </div>
  <div class="rule" style="left:755px;top:639px;width:282px"></div>

  <div class="news-item" style="top:652px">
    <div class="news-thumb"><span role="img" aria-label="News thumbnail, magenta abstract lights" style="background:radial-gradient(circle,#d23ad0,#4a0a4e)"></span></div>
    <p class="news-text">Sed ut perspiciatis unde omnis iste natus error sit voluptatem accusantium doloremque laudantium, totam rem aperiam.</p>
  </div>
  <div class="rule" style="left:755px;top:710px;width:282px"></div>

  <div class="news-item" style="top:724px">
    <div class="news-thumb"><span role="img" aria-label="News thumbnail, colourful wave stripes" style="background:linear-gradient(160deg,#4aa8d8,#f0e040 55%,#d84a8a)"></span></div>
    <p class="news-text">At vero eos et accusamus et iusto odio dignissimos ducimus qui blanditiis praesentium.</p>
  </div>
  <div class="rule" style="left:755px;top:784px;width:282px"></div>

  <div class="btn-blue" style="left:756px;top:794px;width:155px">Visit our Blog
    <svg width="18" height="6" viewBox="0 0 18 6"><line x1="0" y1="3" x2="15" y2="3" stroke="#fff" stroke-dasharray="1.5 1.5"/><polygon points="14,0 18,3 14,6" fill="#fff"/></svg>
  </div>

  <footer class="footer"></footer>

  <h3 class="footer-head" style="left:94px;top:880px">Newsletter</h3>
  <div class="footer-rule" style="left:95px;top:910px;width:307px"></div>
  <p class="footer-text" style="left:95px;top:922px">At vero eos et accusamus et iusto odio dignissimos ducimus qui blanditiis praesentium</p>
  <div class="email-field">your email address</div>
  <div class="btn-blue" style="left:95px;top:1010px;width:169px;height:32px">Subscribe
    <svg width="18" height="6" viewBox="0 0 18 6"><line x1="0" y1="3" x2="15" y2="3" stroke="#fff" stroke-dasharray="1.5 1.5"/><polygon points="14,0 18,3 14,6" fill="#fff"/></svg>
  </div>

  <h3 class="footer-head" style="left:493px;top:880px">Social Connection</h3>
  <div class="footer-rule" style="left:497px;top:910px;width:304px"></div>
  <p class="footer-text" style="left:497px;top:920px">At vero eos et accusamus et iusto odio dignissimos ducimus qui blanditiis praesentium</p>
  <div class="social">
    <span style="background:#e2622a"></span>
    <span style="background:#46689e"></span>
    <span style="background:#3f8fc9"></span>
    <span style="background:#c8312c"></span>
    <span style="background:#5fbcd0"></span>
  </div>

  <div class="brand brand--footer">
    <span class="brand-square"></span>
    <span class="brand-name">NORAVI CONSULTING</span>
  </div>
</body>
</html>
```